Community-based social network needs a new landing page

We need a landing page for a local social network in Singapore called "LaneKindred.sg". It is a website that help neighbours to connect with each other for mutual benefits such as providing professional/non-professional services, sharing items, and neighbourly help, etc.

There is an existing website but we want to completely revamp it. It is most important that the new landing page communicates that the neighbourhood has skills and services for people to discover.

The final design of the landing page should be modern, and communicates a sense of community and vibrancy. As a matter of priority, more real estate should be accorded to the neighbours providing services elements.

We have drafted 2 reference sites that communicates the key ideas/user propositions for your easy reference:
http://tarvelquin8.example-sites.com/lanekindred
http://tarvelquin8.example-sites.com/lanekindred2

As long as the key ideas/user propositions are kept to, we are open to any design proposals. I.e. you do not have to follow the design layout of the reference sites

Target Market(s)

Our target market is primarily the Singapore community, includes all genders, education levels and occupations, aged between 17-45 years old.

In the file uploaded, you will find pictures of Singapore neighbourhoods and people of local ethnicities. Please use them, but you may arrange and add further filters to better enhance them

Industry/Entity Type

Real Estate

Requirements
Nice to have
• Landing page could be similar to that of www.gatherloft.com, not just at the top, but also the way the other categories are presented at the bottom.

```html
<!DOCTYPE html>
<html lang="en">
<head>
<meta charset="utf-8">
<title>LaneKindred.sg — Neighbours helping neighbours</title>
<link href="https://fonts.googleapis.com/css2?family=Arimo:wght@400;700&family=Archivo+Narrow:wght@400;600&display=swap" rel="stylesheet">
<style>
  :root{
    --red:#c9372a;
    --red-dark:#b52e22;
    --tan:#c49a6c;
    --brown:#4b3b2f;
    --brown-text:#5a4330;
    --page:#f0f0f0;
    --white:#ffffff;
    --field:#eceef0;
    --ink:#222222;
    --panel:rgba(235,238,242,0.88);
  }
  *{box-sizing:border-box;margin:0;padding:0}
  html,body{width:1017px;height:1200px;overflow:hidden}
  body{position:relative;background:var(--page);font-family:"Arimo",Arial,sans-serif;color:var(--ink)}
  .abs{position:absolute}

  /* Header */
  .site-header{left:0;top:0;width:1017px;height:102px;background:var(--red)}
  .brand{left:32px;top:20px;width:212px;height:44px;background:var(--white);display:flex;align-items:center;justify-content:center;gap:8px;font-weight:700;font-size:23px;color:var(--red);letter-spacing:-0.5px}
  .brand-dot{width:14px;height:14px;background:var(--red)}
  .header-social{left:895px;top:70px;width:32px;height:32px;background:var(--white)}
  .header-social span{position:absolute;left:10px;top:9px;width:12px;height:14px;background:var(--red)}
  .header-login{left:932px;top:70px;width:58px;height:32px;background:var(--white);color:var(--red);font-weight:700;font-size:16px;display:flex;align-items:center;justify-content:center}

  /* Hero */
  .hero{left:0;top:102px;width:1017px;height:498px;
    background:
      linear-gradient(180deg,rgba(0,0,0,0) 60%,rgba(40,70,30,0.9) 100%),
      linear-gradient(90deg,#5f7fa0 0%,#8aa7c2 25%,#cfc9b8 45%,#e7e1d0 60%,#ddd6c2 80%,#8aa3bd 100%);}
  .panel{background:var(--panel);border-radius:3px}
  .field{position:absolute;background:var(--field);font-size:12.5px;color:#333;padding-left:9px;display:flex;align-items:center}
  .btn{position:absolute;background:var(--red);color:var(--white);font-size:12px;display:flex;align-items:center;justify-content:center}
  .login-panel{left:41px;top:117px;width:173px;height:102px}
  .signup-panel{left:41px;top:249px;width:213px;height:165px}
  .signup-title{position:absolute;left:10px;top:10px;color:var(--red);font-size:13px}

  .offer-photo{border-radius:50%;border:3px solid var(--white)}
  .offer-label{background:rgba(238,240,243,0.9);font-size:10.5px;line-height:14px;color:#111;padding:4px 6px 0 8px}

  /* Categories */
  .category .back{position:absolute;background:var(--red)}
  .category .front{position:absolute;background:var(--tan);text-align:center}
  .cat-title{font-family:"Archivo Narrow","Arial Narrow",sans-serif;color:var(--red);font-size:16px;line-height:20px;padding:0 8px 6px;border-bottom:1px dashed var(--brown-text);margin:0 8px}
  .cat-body{font-size:12px;line-height:14.5px;color:var(--brown-text);padding:8px 18px 0}
  .cat-go{position:absolute;left:50%;transform:translateX(-50%);width:40px;height:25px;background:var(--red);color:var(--white);font-size:12px;display:flex;align-items:center;justify-content:center}

  .divider{left:0;top:824px;width:1017px;border-top:1px dashed var(--red)}
  .footer-nav{left:0;top:843px;width:1017px;display:flex;justify-content:center;gap:34px;font-size:11px;color:var(--red)}
  .footer-nav a{color:inherit;text-decoration:none}

  .block-title{font-weight:700;font-size:16px;color:var(--red);letter-spacing:0.2px}
  .media{left:59px;top:900px;width:300px}
  .media p{font-size:12.5px;line-height:16px;color:var(--red);margin-top:4px}
  .posts{left:395px;top:884px;width:250px}
  .post{position:absolute;left:0;display:flex;gap:10px;font-size:10.5px;line-height:14px;color:#111}
  .post svg{flex:none}
  .members{left:696px;top:880px}
  .member-grid{position:absolute;left:0;top:32px;display:grid;grid-template-columns:repeat(6,34px);grid-auto-rows:34px;gap:2px}
  .member-grid div{width:34px;height:34px}

  /* Footer */
  .site-footer{left:0;top:1088px;width:1017px;height:112px;background:var(--brown);color:var(--white)}
  .legal{position:absolute;left:20px;top:42px;width:520px;font-size:9.5px;line-height:13px}
  .keep{position:absolute;left:860px;top:16px;font-weight:700;font-size:16px}
  .social{position:absolute;top:40px;width:33px;height:33px;background:var(--red)}
</style>
</head>
<body>

<header class="site-header abs">
  <div class="brand abs"><span class="brand-dot"></span>LaneKindred.sg</div>
  <div class="header-social abs" aria-label="Social sign in"><span></span></div>
  <div class="header-login abs">Login</div>
</header>

<section class="hero abs" role="img" aria-label="Photo of Singapore housing blocks under a cloudy blue sky with trees in front"></section>

<form class="login-panel panel abs">
  <div class="field" style="left:11px;top:8px;width:151px;height:24px">Username</div>
  <div class="field" style="left:11px;top:45px;width:151px;height:24px">Password</div>
  <div class="btn" style="left:112px;top:78px;width:50px;height:20px">Login</div>
</form>

<form class="signup-panel panel abs">
  <div class="signup-title">Sign up</div>
  <div class="field" style="left:9px;top:31px;width:192px;height:24px">Display Name</div>
  <div class="field" style="left:9px;top:64px;width:192px;height:24px">Email Address</div>
  <div class="field" style="left:9px;top:96px;width:192px;height:24px">Password</div>
  <div class="btn" style="left:9px;top:131px;width:32px;height:26px"><span style="width:10px;height:12px;background:#fff;display:block"></span></div>
  <div class="btn" style="left:43px;top:131px;width:68px;height:26px;font-size:14px">Connect</div>
  <div class="btn" style="left:117px;top:131px;width:90px;height:26px">Create Account</div>
</form>

<div class="offer-photo abs" role="img" aria-label="Portrait of Aileen, a housekeeper" style="left:637px;top:123px;width:70px;height:70px;background:radial-gradient(#7da35c,#3f6c2c)"></div>
<div class="offer-label abs" style="left:707px;top:133px;width:140px;height:35px">Aileen is offering hourly housekeeping at $13 per hour</div>

<div class="offer-photo abs" role="img" aria-label="Portrait of Min, a beautician" style="left:755px;top:219px;width:86px;height:86px;background:radial-gradient(#c9b3a6,#4a3c36)"></div>
<div class="offer-label abs" style="left:838px;top:238px;width:147px;height:56px;padding-left:10px">Min is offering professional home-call beauty services at low rates</div>

<div class="offer-photo abs" role="img" aria-label="Portrait of Hui Ling, an architecture student" style="left:757px;top:333px;width:78px;height:78px;background:radial-gradient(#dcdde2,#6f7a8c)"></div>
<div class="offer-label abs" style="left:838px;top:350px;width:147px;height:58px;padding-left:10px">Hui Ling, an architecture undergraduate, will design your home from only $200</div>

<div class="offer-photo abs" role="img" aria-label="Portrait of Jas with her dog" style="left:638px;top:454px;width:84px;height:84px;background:radial-gradient(#c08a58,#5a3c26)"></div>
<div class="offer-label abs" style="left:722px;top:478px;width:140px;height:48px">Jas is offering dog walking at $10 per hour</div>

<section class="category">
  <div class="back" style="left:120px;top:617px;width:220px;height:190px;transform:rotate(-3deg)"></div>
  <div class="front" style="left:125px;top:621px;width:214px;height:183px;padding-top:17px">
    <div class="cat-title">Professional Services</div>
    <p class="cat-body">If you're a professional service provider, take a FREE listing here and offer a "neighbour rate" to the people living near you!</p>
    <div class="cat-go" style="top:150px">GO</div>
  </div>
</section>
<section class="category">
  <div class="back" style="left:395px;top:617px;width:220px;height:190px;transform:rotate(-3deg)"></div>
  <div class="front" style="left:399px;top:621px;width:214px;height:183px;padding-top:17px">
    <div class="cat-title">Non-Professional</div>
    <p class="cat-body">You may be a student, enthusiast or just someone with time and muscle, but you may be good enough for your neighbours to hire! Take a FREE listing here!</p>
    <div class="cat-go" style="top:150px">GO</div>
  </div>
</section>
<section class="category">
  <div class="back" style="left:663px;top:617px;width:220px;height:190px;transform:rotate(-3deg)"></div>
  <div class="front" style="left:663px;top:621px;width:214px;height:183px;padding-top:5px">
    <div class="cat-title">Selling, helping, lending<br>and borrowing</div>
    <p class="cat-body">Let's contribute stuff and effort into the neighbourhood pool. We can all save money, reduce wastage and be kind to the environment.</p>
    <div class="cat-go" style="top:150px">GO</div>
  </div>
</section>

<div class="divider abs"></div>
<nav class="footer-nav abs">
  <a href="#">ABOUT US</a><a href="#">FAQ</a><a href="#">TERMS OF USE</a><a href="#">PRIVACY POLICY</a><a href="#">CONTACT US</a>
</nav>

<section class="media abs">
  <h3 class="block-title">MEDIA MENTIONS</h3>
  <p>"Website to help neighbours share household items"<br>- The Harbour Ledger</p>
</section>

<section class="posts abs">
  <h3 class="block-title">LATEST POSTS</h3>
  <div class="post" style="top:27px">
    <svg width="34" height="24" viewBox="0 0 34 24"><rect x="2" y="6" width="12" height="16" rx="2" fill="#5a4330" transform="rotate(-20 8 14)"/><rect x="16" y="4" width="12" height="16" rx="2" fill="#5a4330" transform="rotate(15 22 12)"/></svg>
    <span style="padding-top:3px">KelvinR is selling Micro/Nano Sim Adapters</span>
  </div>
  <div class="post" style="top:55px">
    <svg width="34" height="34" viewBox="0 0 34 34"><polygon points="22,1 8,19 16,19 4,33 28,13 19,13 30,1" fill="#5a4330"/></svg>
    <span style="padding-top:9px">TKS wants to offer Electrical Repair (DIY)</span>
  </div>
  <div class="post" style="top:88px">
    <svg width="34" height="28" viewBox="0 0 34 28"><path d="M8 10h16v14H8z" fill="#5a4330"/><path d="M24 14l9-8" stroke="#5a4330" stroke-width="3"/><path d="M8 13c-6 0-6 8 0 8" stroke="#5a4330" stroke-width="2" fill="none"/></svg>
    <span style="width:215px">Benny Tan wants to offer help water your plants while you're overseas! I'm dependable and detailed.</span>
  </div>
  <div class="post" style="top:142px">
    <svg width="34" height="30" viewBox="0 0 34 30"><path d="M13 1L9 29M21 1L17 29M12 8h8M11 15h8M10 22h8" stroke="#5a4330" stroke-width="2.5" fill="none"/></svg>
    <span style="padding-top:10px">FarisM has shared Ladder</span>
  </div>
</section>

<section class="members abs">
  <h3 class="block-title">LATEST MEMBERS</h3>
  <div class="member-grid" role="img" aria-label="Grid of profile photos of the newest members">
    <div style="background:#8a8f95"></div><div style="background:#6a7a62"></div><div style="background:#b5b5b5"></div><div style="background:#2e2a3c"></div><div style="background:#7a6452"></div><div style="background:#e0c8d8"></div>
    <div style="background:#8c7c6e"></div><div style="background:#9aa3ad"></div><div style="background:#bfc8d2"></div><div style="background:#c98a5a"></div><div style="background:#c7c2a8"></div><div style="background:#d0cfc6"></div>
    <div style="background:#7a5540"></div><div style="background:#4e5a48"></div><div style="background:#5d6b7a"></div><div style="background:#a07a6a"></div><div style="background:#b89a86"></div><div style="background:#4a4040"></div>
    <div style="background:#5a6470"></div><div style="background:#3a3a44"></div><div style="background:#6e6e6e"></div><div style="background:#9a7f66"></div><div style="background:#8c5aa0"></div><div style="background:#2b2b2b"></div>
  </div>
</section>

<footer class="site-footer abs">
  <p class="legal">© Kinnerhaus Pte Ltd 2013<br>LaneKindred.sg is a website of Kinnerhaus Pte Ltd. We help you pool together physical items, efforts, and purchasing power with your favourite neighbours so that you can save money, free up space at home, be eco-friendly.</p>
  <div class="keep">KEEP IN TOUCH</div>
  <div class="social" style="left:859px" aria-label="Social link"></div>
  <div class="social" style="left:901px" aria-label="Social link"></div>
  <div class="social" style="left:944px" aria-label="Social link"></div>
</footer>

</body>
</html>
```